Global Beard Oil Review Business needs a refresh

topwhiskertonic.net is a global business who's mission is to curate all available beard oils from around the world, review and grade them and present this curated collection to the user of the website.

The scope of this job includes the web site design and the design of a suitable logo to be used in the site header.

The existing site can be seen on http://topwhiskertonic.net, however this is a mock-up only the style and logo should NOT be used. This is to give you an idea of the concept of the site only.

This job is for PSD design only.

See attached design brief for detailed design requirements.
Updates

Project Deadline Extended
Reason: Extending deadline by 5 days to allow for final submissions

Target Market(s)

Men's grooming / retail

Industry/Entity Type

Retail

Number of Pages Required

2 page

Font styles to use
Sans Serif

Requirements
Must have
• 1) Comparison Table
• 2) Side Bar
• 3) Header area
• 4) Photo of Delvin Marsk (attached - can be circular or "cut-out")
• 5) Cool beard-oriented custom design background (e.g., stylistic black/brown on brown/orange beard background. I envision this beard background "drawing" rather than photo based)
• (see attached design requirements for details)
Nice to have
• Signature style writing at top with name "Delvin Marsk"
Should not have
• Do NOT use the look & feel or logo from the existing site.

```html
<!DOCTYPE html>
<html lang="en">
<head>
<meta charset="utf-8">
<title>Top Whisker Tonic</title>
<link href="https://fonts.googleapis.com/css2?family=Raleway:wght@400;600;700&family=Roboto+Condensed:wght@400&family=Lato:wght@400;700&family=Great+Vibes&display=swap" rel="stylesheet">
<style>
:root{
  --ink:#2f3a43;
  --teal:#3fb3b1;
  --orange:#f7922f;
  --text:#3b3b3b;
  --page:#f6f6f6;
  --row-a:#e9e9e9;
  --row-b:#f5f5f5;
  --line:#c9c9c9;
  --white:#ffffff;
}
*{margin:0;padding:0;box-sizing:border-box}
html,body{width:886px;height:1200px;overflow:hidden}
body{position:relative;background:var(--page);font-family:'Lato',sans-serif;color:var(--text)}
.abs{position:absolute}
.cond{font-family:'Roboto Condensed',sans-serif}
.raleway{font-family:'Raleway',sans-serif}

.site-header{left:0;top:0;width:886px;height:79px;background:var(--ink);border-bottom:1px solid #55616b}
.brand{left:146px;top:26px;display:flex;align-items:center;gap:8px;font-family:'Lato',sans-serif;font-weight:700;font-size:19px;color:var(--teal);letter-spacing:.5px}
.brand .dot{width:14px;height:14px;border-radius:50%;background:var(--teal)}
.nav{top:30px;left:366px;display:flex;align-items:center;font-size:12px;color:var(--white)}
.nav a{color:var(--white);text-decoration:none;margin-right:19px}
.nav .active{border:1.5px solid var(--teal);color:var(--teal);border-radius:3px;padding:3px 9px;margin-right:17px}

.hero{left:0;top:79px;width:886px;height:305px;background:linear-gradient(100deg,#8c4d14 0%,#c8801f 35%,#d89332 60%,#b86c18 100%)}
.hero-title{left:146px;top:164px;font-family:'Raleway',sans-serif;font-size:28px;line-height:28px;color:var(--white)}
.hero-title .o{color:var(--orange);font-weight:700}
.hero-title .t{color:var(--teal)}
.btn{position:absolute;font-family:'Roboto Condensed',sans-serif;font-size:11px;border-radius:3px;text-align:center;line-height:19px;height:22px}
.btn-light{border:1.5px solid var(--white);color:var(--white)}
.btn-teal{border:1.5px solid var(--teal);color:var(--teal);background:var(--white)}
.dots{left:425px;top:357px;display:flex;gap:7px}
.dots span{width:9px;height:9px;border-radius:50%;background:var(--white)}
.dots span:first-child{background:var(--ink)}

.heading{font-family:'Raleway',sans-serif;font-size:23px;color:var(--teal)}
.heading .o{color:var(--orange)}
.rule{height:1px;background:var(--line)}
.copy{font-size:8.7px;line-height:11.6px}

.review{left:147px;top:743px;width:395px;border-collapse:collapse;font-size:8.5px}
.review th{background:var(--teal);color:var(--white);font-family:'Roboto Condensed',sans-serif;font-weight:400;font-size:9.5px;height:29px;border-right:1px solid #7fd0cf}
.review td{height:61px;vertical-align:middle;border-right:1px solid #d7d7d7}
.review tr:nth-child(odd) td{background:var(--row-a)}
.review tr:nth-child(even) td{background:var(--row-b)}
.review .k{color:var(--orange);font-weight:700;font-family:'Roboto Condensed',sans-serif;font-size:10px}
.review .name{padding-left:6px;line-height:16px}
.review .bottle{width:36px;height:44px;margin:0 auto;background:linear-gradient(#444,#111);border:2px solid #fff;box-shadow:0 0 0 1px #ccc}
.review .origin{padding-left:8px;line-height:15.5px}
.review .score{text-align:right;padding-right:18px;line-height:15.5px;font-family:'Roboto Condensed',sans-serif;font-size:10px}
.review .score b{font-weight:400;display:inline-block;width:24px;text-align:left;padding-left:9px;font-family:'Lato',sans-serif;font-size:8.5px}
.buy{display:block;margin:0 auto;width:43px;height:17px;border-radius:3px;background:var(--orange);color:var(--white);font-size:7.8px;text-align:center;line-height:17px;box-shadow:0 1px 0 #c46a15}

.sidebar{left:554px;top:402px;width:186px;height:655px;background:var(--white);box-shadow:0 0 6px rgba(0,0,0,.15);border-radius:3px}
.portrait-frame{left:10px;top:11px;width:165px;height:178px;border:1px solid #d0d0d0;padding:5px}
.portrait{width:100%;height:100%;background:linear-gradient(135deg,#9a9a9a,#4a4a4a)}
.signature{left:0;top:193px;width:186px;text-align:center;font-family:'Great Vibes',cursive;font-size:22px;color:#222}
.date{width:33px;height:30px;background:var(--orange);color:var(--white);font-size:9px;line-height:12px;text-align:center;padding-top:3px;font-weight:700}
.date sup{font-size:6px}
.post-title{font-size:8.2px;font-weight:700;line-height:12px;color:#222}
.post-img{width:163px;height:54px;border:1px solid #cfcfcf;padding:2px}
.post-img div{width:100%;height:100%}
.post-copy{font-size:8.6px;line-height:11.5px}
.post-copy span{color:var(--orange)}

.footer-links{left:0;top:1090px;width:886px;height:38px;background:var(--orange);color:var(--white);font-size:9px;text-align:center;line-height:38px}
.site-footer{left:0;top:1128px;width:886px;height:72px;background:var(--ink)}
.follow{left:582px;top:23px;color:var(--white);font-family:'Raleway',sans-serif;font-weight:700;font-size:13px}
.socials{left:655px;top:22px;display:flex;gap:5px}
.socials span{width:18px;height:18px;border-radius:50%;background:var(--white)}
.copyright{left:167px;top:51px;font-size:7.5px;color:#ddd}
</style>
</head>
<body>

<header class="site-header abs">
  <div class="brand abs"><span class="dot"></span>Top Whisker Tonic</div>
  <nav class="nav abs cond">
    <a class="active">Home</a><a>About Me</a><a>Our Charter</a><a>Beard Oil Methodology</a><a>BLog</a>
  </nav>
</header>

<section class="hero abs" role="img" aria-label="Burlap drawstring pouch of beard oil on a sunlit wooden table"></section>
<h1 class="hero-title abs"><span class="o">Ridgeline Drifter</span> Man<br>Beard Oil by <span class="t">Kettle Hollow</span><br><span class="t">Grooming</span></h1>
<div class="btn btn-light" style="left:147px;top:270px;width:66px">Read More</div>
<div class="dots abs"><span></span><span></span><span></span></div>

<h2 class="heading abs" style="left:148px;top:408px">About <span class="o">Delvin Marsk</span></h2>
<div class="rule abs" style="left:147px;top:438px;width:395px"></div>
<p class="copy abs" style="left:148px;top:450px;width:395px">Sed ut perspiciatis unde omnis iste natus error sit voluptatem accusantium doloremque laudantium, totam rem aperiam, eaque ipsa quae ab illo inventore veritatis et quasi architecto beatae vitae dicta sunt explicabo. Nemo enim ipsam voluptatem quia voluptas sit aspernatur aut odit aut fugit, sed quia consequuntur magni dolores eos qui ratione voluptatem sequi nesciunt. Neque porro quisquam est, qui dolorem ipsum quia dolor sit amet, consectetur, adipisci velit, sed quia non numquam eius modi tempora incidunt ut labore et dolore magnam aliquam quaerat voluptatem.</p>
<p class="copy abs" style="left:148px;top:538px;width:395px">Sed ut perspiciatis unde omnis iste natus error sit voluptatem accusantium doloremque laudantium, totam rem aperiam, eaque ipsa quae ab illo inventore veritatis et quasi architecto beatae vitae dicta sunt explicabo.</p>
<div class="btn btn-teal" style="left:147px;top:586px;width:71px">Read More</div>

<h2 class="heading abs" style="left:148px;top:648px">The World's #1 <span class="o">Beard Oil Authority</span></h2>
<div class="rule abs" style="left:147px;top:684px;width:395px"></div>
<p class="copy abs" style="left:148px;top:694px;width:380px;line-height:12.5px">Here is the master list of beard oils reviewed to date. You can link directly to the corresponding review by clicking on the name of the beard oil. In accordance with our charter, we are actively working to locate and review every single beard oil available on the planet Earth.</p>

<table class="review abs">
  <colgroup><col style="width:92px"><col style="width:56px"><col style="width:111px"><col style="width:74px"><col style="width:62px"></colgroup>
  <thead><tr><th>Supplier &amp; Name</th><th>Photo</th><th>Origin,Base Oil,Scent</th><th style="line-height:10px">Affect,Value,<br>Overall</th><th style="border-right:0">Links</th></tr></thead>
  <tbody>
    <tr><td class="name"><span class="k">S:</span> Gruff Harbor<br><span class="k">N:</span> Timberline</td><td><div class="bottle" role="img" aria-label="Beard oil bottle"></div></td><td class="origin"><span class="k" style="color:#333">O:</span> Spiciatis<br><span class="k" style="color:#333">B:</span> Modi Tempora<br><span class="k" style="color:#333">S:</span> Quia</td><td class="score">Affect:<b>7</b><br>Value:<b>5</b><br>Overall:<b>5</b></td><td><span class="buy">Buy Now</span></td></tr>
    <tr><td class="name"><span class="k">S:</span> Gruff Harbor<br><span class="k">N:</span> Timberline</td><td><div class="bottle" role="img" aria-label="Beard oil bottle"></div></td><td class="origin"><span class="k" style="color:#333">O:</span> Spiciatis<br><span class="k" style="color:#333">B:</span> Modi Tempora<br><span class="k" style="color:#333">S:</span> Quia</td><td class="score">Affect:<b>7</b><br>Value:<b>5</b><br>Overall:<b>5</b></td><td><span class="buy">Buy Now</span></td></tr>
    <tr><td class="name"><span class="k">S:</span> Gruff Harbor<br><span class="k">N:</span> Timberline</td><td><div class="bottle" role="img" aria-label="Beard oil bottle"></div></td><td class="origin"><span class="k" style="color:#333">O:</span> Spiciatis<br><span class="k" style="color:#333">B:</span> Modi Tempora<br><span class="k" style="color:#333">S:</span> Quia</td><td class="score">Affect:<b>7</b><br>Value:<b>5</b><br>Overall:<b>5</b></td><td><span class="buy">Buy Now</span></td></tr>
    <tr><td class="name"><span class="k">S:</span> Gruff Harbor<br><span class="k">N:</span> Timberline</td><td><div class="bottle" role="img" aria-label="Beard oil bottle"></div></td><td class="origin"><span class="k" style="color:#333">O:</span> Spiciatis<br><span class="k" style="color:#333">B:</span> Modi Tempora<br><span class="k" style="color:#333">S:</span> Quia</td><td class="score">Affect:<b>7</b><br>Value:<b>5</b><br>Overall:<b>5</b></td><td><span class="buy">Buy Now</span></td></tr>
  </tbody>
</table>

<div class="btn btn-teal" style="left:147px;top:1034px;width:71px">Load More</div>
<svg class="abs" style="left:227px;top:1034px" width="22" height="22" viewBox="0 0 22 22" aria-label="Reload">
  <path d="M6 7 A7 7 0 1 1 4.5 13" fill="none" stroke="#111" stroke-width="2.2"/>
  <path d="M2 5 L7.5 4.5 L6.5 10 Z" fill="#111"/>
</svg>

<aside class="sidebar abs">
  <div class="portrait-frame abs"><div class="portrait" role="img" aria-label="Black and white photo of Delvin Marsk giving a thumbs up"></div></div>
  <div class="signature abs">Delvin Marsk</div>
  <h2 class="heading abs" style="left:12px;top:252px">Latest <span class="o">Blog</span></h2>
  <div class="rule abs" style="left:11px;top:282px;width:163px"></div>

  <div class="date abs" style="left:10px;top:297px">12<sup>th</sup><br>Feb</div>
  <div class="post-title abs" style="left:50px;top:300px;width:130px">Lorem ipsum dolor sit amet, consectetuer</div>
  <div class="post-img abs" style="left:10px;top:334px"><div role="img" aria-label="Dropper releasing beard oil over a green background" style="background:linear-gradient(90deg,#3d5a2a,#7a8a4a,#8a5a3a)"></div></div>
  <p class="post-copy abs" style="left:10px;top:394px;width:170px">Sed ut perspiciatis unde omnis iste natus error sit voluptatem accusantium dolor emque laudantium, <span>+</span></p>
  <div class="rule abs" style="left:10px;top:438px;width:165px;background:#e3e3e3"></div>

  <div class="date abs" style="left:10px;top:458px">12<sup>th</sup><br>Feb</div>
  <div class="post-title abs" style="left:50px;top:461px;width:130px">Lorem ipsum dolor sit amet, consectetuer</div>
  <div class="post-img abs" style="left:10px;top:494px"><div role="img" aria-label="Beard oil bottle standing on sand" style="background:linear-gradient(90deg,#c9b48a,#b39a6a,#d5c39c)"></div></div>
  <p class="post-copy abs" style="left:10px;top:555px;width:170px">Sed ut perspiciatis unde omnis iste natus error sit voluptatem accusantium dolor emque laudantium, <span>+</span></p>
  <div class="rule abs" style="left:10px;top:598px;width:165px;background:#e3e3e3"></div>

  <div class="btn btn-teal" style="left:11px;top:610px;width:72px">Read All</div>
</aside>

<nav class="footer-links abs">Home &nbsp;| &nbsp;About Me &nbsp;| &nbsp;Our Charter &nbsp;| &nbsp;Beard Oil Methodology &nbsp;| &nbsp;Blog</nav>

<footer class="site-footer abs">
  <svg class="abs" style="left:166px;top:16px" width="50" height="26" viewBox="0 0 50 26" aria-label="Contact">
    <circle cx="13" cy="13" r="12" fill="#f7922f"/>
    <rect x="9" y="6" width="8" height="14" rx="1.5" fill="none" stroke="#fff" stroke-width="1.4"/>
    <circle cx="13" cy="17.5" r="0.9" fill="#fff"/>
    <circle cx="36" cy="13" r="12" fill="#45505a"/>
    <rect x="29" y="9" width="14" height="9" fill="none" stroke="#fff" stroke-width="1.3"/>
    <path d="M29 9 L36 14.5 L43 9" fill="none" stroke="#fff" stroke-width="1.3"/>
  </svg>
  <div class="brand abs" style="left:224px;top:20px;font-size:16px"><span class="dot" style="width:12px;height:12px"></span>Top Whisker Tonic</div>
  <div class="copyright abs">Copyright © 2016 Top Whisker Tonic. All rights reserved.</div>
  <div class="follow abs">Follow Us</div>
  <div class="socials abs"><span></span><span></span><span></span><span></span></div>
</footer>

</body>
</html>
```